Opening a Hair Salon

Looking for a design for my sign that looks high end, an emphasis on color but welcoming to men and women.

The name is Corvane Haircuts and Colors

Trying capture a more affluent client. Looking for a very modern look.

Reason: Time is going to quick and would like to see a few more options.

```html
<!DOCTYPE html>
<html lang="en">
<head>
<meta charset="utf-8">
<title>Corvane Haircuts and Colors – Sign Options</title>
<link rel="stylesheet" href="https://fonts.googleapis.com/css2?family=Oswald:wght@500&family=Roboto:wght@500;700&display=swap">
<style>
  :root {
    --stage-dark: #0b1624;
    --stage-light: #2a4d72;
    --paper: #ffffff;
    --ink: #111111;
    --hair-light: #b9805a;
    --hair-mid: #8a4f2c;
    --hair-dark: #4a2414;
  }
  html, body { margin: 0; padding: 0; overflow: hidden; }
  body {
    width: 778px; height: 1200px;
    background: linear-gradient(120deg, var(--stage-dark) 0%, #16283f 45%, var(--stage-light) 100%);
    position: relative;
    font-family: "Roboto", Arial, sans-serif;
  }
  .sign {
    position: absolute; left: 44px; width: 689px; height: 172px;
    background: var(--paper); overflow: hidden;
    box-shadow: 0 4px 14px rgba(0,0,0,.45);
  }
  .sign--magenta { top: 25px;   --accent: #d81f9c; --deep: #5c0f47; --soft: #f07ad4; }
  .sign--violet  { top: 221px;  --accent: #3417cf; --deep: #1f1060; --soft: #7d74f0; }
  .sign--red     { top: 415px;  --accent: #cc1119; --deep: #5c0b0d; --soft: #f06a8a; }
  .sign--amber   { top: 612px;  --accent: #d67f17; --deep: #5c3a11; --soft: #f7a070; }
  .sign--cyan    { top: 809px;  --accent: #1898cf; --deep: #154760; --soft: #5fe0f2; }
  .sign--lime    { top: 1003px; --accent: #66cc16; --deep: #2c5c10; --soft: #b8f060; }

  .sign__swoosh {
    position: absolute; left: 0; top: 0; width: 150px; height: 172px;
    background: linear-gradient(90deg, var(--soft) 0%, rgba(255,255,255,0) 100%);
    opacity: .7;
  }

  .brand { position: absolute; left: 26px; top: 34px; display: flex; align-items: center; gap: 10px; color: var(--deep); font-weight: 500; }
  .brand__dot { width: 30px; height: 30px; border-radius: 50%; background: var(--accent); flex: none; }
  .brand__name { line-height: 1; }
  .brand__word { display: block; font-size: 44px; letter-spacing: .5px; }
  .brand__line { display: block; font-size: 12px; letter-spacing: .6px; margin-top: 4px; text-transform: uppercase; }

  .offer { position: absolute; left: 232px; width: 280px; top: 24px; text-align: center; color: var(--accent); font-weight: 500; font-size: 23px; line-height: 25px; text-transform: uppercase; margin: 0; }
  .call { position: absolute; left: 226px; width: 290px; top: 98px; text-align: center; margin: 0; }
  .call__prompt { display: block; font-weight: 700; font-size: 16px; color: var(--ink); letter-spacing: .1px; }
  .call__phone { display: block; font-family: "Oswald", "Arial Narrow", sans-serif; font-weight: 500; font-size: 46px; line-height: 50px; color: var(--deep); letter-spacing: .5px; }

  .portrait {
    position: absolute; right: 0; top: 0; width: 180px; height: 172px;
    background:
      radial-gradient(ellipse at 40% 35%, var(--hair-light) 0%, var(--hair-mid) 45%, transparent 75%),
      linear-gradient(100deg, rgba(255,255,255,0) 0%, var(--hair-mid) 35%, var(--hair-dark) 100%);
  }
</style>
</head>
<body>

<section class="sign sign--magenta">
  <div class="sign__swoosh" role="img" aria-label="Soft flowing silk ribbon in magenta tones"></div>
  <div class="brand"><span class="brand__dot"></span><span class="brand__name"><span class="brand__word">Corvane</span><span class="brand__line">Haircuts and Colors</span></span></div>
  <p class="offer">We offer the<br>best style in town</p>
  <p class="call"><span class="call__prompt">MAKE AN APPOINTMENT TODAY!</span><span class="call__phone">310-5824-617</span></p>
  <div class="portrait" role="img" aria-label="Photo of a model with long glossy brown hair"></div>
</section>

<section class="sign sign--violet">
  <div class="sign__swoosh" role="img" aria-label="Soft flowing silk ribbon in violet tones"></div>
  <div class="brand"><span class="brand__dot"></span><span class="brand__name"><span class="brand__word">Corvane</span><span class="brand__line">Haircuts and Colors</span></span></div>
  <p class="offer">We offer the<br>best style in town</p>
  <p class="call"><span class="call__prompt">MAKE AN APPOINTMENT TODAY!</span><span class="call__phone">310-5824-617</span></p>
  <div class="portrait" role="img" aria-label="Photo of a model with long glossy brown hair"></div>
</section>

<section class="sign sign--red">
  <div class="sign__swoosh" role="img" aria-label="Soft flowing silk ribbon in red and pink tones"></div>
  <div class="brand"><span class="brand__dot"></span><span class="brand__name"><span class="brand__word">Corvane</span><span class="brand__line">Haircuts and Colors</span></span></div>
  <p class="offer">We offer the<br>best style in town</p>
  <p class="call"><span class="call__prompt">MAKE AN APPOINTMENT TODAY!</span><span class="call__phone">310-5824-617</span></p>
  <div class="portrait" role="img" aria-label="Photo of a model with long glossy brown hair"></div>
</section>

<section class="sign sign--amber">
  <div class="sign__swoosh" role="img" aria-label="Soft flowing silk ribbon in peach tones"></div>
  <div class="brand"><span class="brand__dot"></span><span class="brand__name"><span class="brand__word">Corvane</span><span class="brand__line">Haircuts and Colors</span></span></div>
  <p class="offer">We offer the<br>best style in town</p>
  <p class="call"><span class="call__prompt">MAKE AN APPOINTMENT TODAY!</span><span class="call__phone">310-5824-617</span></p>
  <div class="portrait" role="img" aria-label="Photo of a model with long glossy brown hair"></div>
</section>

<section class="sign sign--cyan">
  <div class="sign__swoosh" role="img" aria-label="Soft flowing silk ribbon in cyan tones"></div>
  <div class="brand"><span class="brand__dot"></span><span class="brand__name"><span class="brand__word">Corvane</span><span class="brand__line">Haircuts and Colors</span></span></div>
  <p class="offer">We offer the<br>best style in town</p>
  <p class="call"><span class="call__prompt">MAKE AN APPOINTMENT TODAY!</span><span class="call__phone">310-5824-617</span></p>
  <div class="portrait" role="img" aria-label="Photo of a model with long glossy brown hair"></div>
</section>

<section class="sign sign--lime">
  <div class="sign__swoosh" role="img" aria-label="Soft flowing silk ribbon in lime tones"></div>
  <div class="brand"><span class="brand__dot"></span><span class="brand__name"><span class="brand__word">Corvane</span><span class="brand__line">Haircuts and Colors</span></span></div>
  <p class="offer">We offer the<br>best style in town</p>
  <p class="call"><span class="call__prompt">MAKE AN APPOINTMENT TODAY!</span><span class="call__phone">310-5824-617</span></p>
  <div class="portrait" role="img" aria-label="Photo of a model with long glossy brown hair"></div>
</section>

</body>
</html>
```